Brekwell Automotive needs a catchy banner design

We need a design for a banner to be displayed on the fence in the outfield of a baseball stadium to show off our company and have people interested in what we do. We need something catchy that's going to attract people to look over at our banner.
We are a
Complete Automotive Service Company
Tires - Service - Repair - Diesel
We are in a Town called Fuquay-Varina
(555)314-2609 we would like the phone number to be a descent size so when you are in the stands you can read it.
I have attached what we came up with but like I said we need it to pop more and make the viewer that's looking at it want to look us up.
The Banner size is 24ft long and 10ft tall

```html
<!DOCTYPE html>
<html lang="en">
<head>
<meta charset="utf-8">
<title>Brekwell Automotive Banner</title>
<link href="https://fonts.googleapis.com/css2?family=Titan+One&family=Audiowide&family=Montserrat:wght@500;800&display=swap" rel="stylesheet">
<style>
  :root {
    --brand-blue: #0d64c8;
    --bright-blue: #1e86f0;
    --navy: #030b3a;
    --black: #050505;
    --white: #ffffff;
    --yellow: #f4de1f;
    --grey: #7a7a75;
    --engine-dark: #1a1a1a;
    --engine-mid: #5a5a5a;
  }
  html, body {
    margin: 0;
    padding: 0;
    width: 1200px;
    height: 500px;
    overflow: hidden;
    background: var(--black);
  }
  .banner {
    position: relative;
    width: 1200px;
    height: 500px;
    background: var(--black);
    overflow: hidden;
  }
  .top-band {
    position: absolute;
    left: 0; top: 0;
    width: 1200px; height: 93px;
    background: var(--brand-blue);
    display: flex;
    align-items: center;
    justify-content: center;
  }
  .tagline {
    margin: 0;
    font-family: "Titan One", sans-serif;
    font-size: 45px;
    letter-spacing: 0.5px;
    word-spacing: 8px;
    color: var(--navy);
    -webkit-text-stroke: 5px var(--white);
    paint-order: stroke fill;
    line-height: 1;
    white-space: nowrap;
  }
  .stage {
    position: absolute;
    left: 0; top: 93px;
    width: 1200px; height: 322px;
  }
  .stage svg { position: absolute; left: 0; top: 0; }
  .services {
    position: absolute;
    left: 22px; top: 72px;
    margin: 0; padding: 0;
    list-style: none;
    font-family: "Audiowide", sans-serif;
    color: var(--white);
    font-size: 72px;
    line-height: 77px;
    text-shadow: 0 3px 6px rgba(0,0,0,0.7);
  }
  .services li { white-space: nowrap; }
  .services .dot { font-size: 48px; vertical-align: 10px; margin-right: 2px; }
  .company-name {
    position: absolute;
    left: 878px; top: 92px;
    width: 272px;
    margin: 0;
    text-align: center;
    font-family: "Audiowide", sans-serif;
    font-size: 32px;
    line-height: 40px;
    color: var(--bright-blue);
  }
  .divider {
    position: absolute;
    left: 0; top: 415px;
    width: 1200px; height: 6px;
    background: var(--brand-blue);
  }
  .contact-band {
    position: absolute;
    left: 0; top: 421px;
    width: 1200px; height: 79px;
    font-family: "Montserrat", sans-serif;
    white-space: nowrap;
  }
  .call-now {
    position: absolute;
    left: 56px; top: 14px;
    font-size: 45px;
    font-weight: 500;
    color: var(--yellow);
    letter-spacing: 1px;
  }
  .phone {
    position: absolute;
    left: 347px; top: 8px;
    font-size: 51px;
    font-weight: 800;
    color: var(--white);
  }
  .town {
    position: absolute;
    left: 799px; top: 16px;
    width: 365px;
    font-size: 39px;
    font-weight: 800;
    color: var(--grey);
  }
</style>
</head>
<body>
<div class="banner">
  <header class="top-band">
    <h1 class="tagline">COMPLETE AUTOMOTIVE SERVICE COMPANY</h1>
  </header>

  <section class="stage">
    <svg width="1200" height="322" viewBox="0 0 1200 322">
      <defs>
        <linearGradient id="engineTone" x1="0" y1="0" x2="1" y2="1">
          <stop offset="0" stop-color="var(--engine-mid)"/>
          <stop offset="0.55" stop-color="var(--engine-dark)"/>
          <stop offset="1" stop-color="#2e2e2e"/>
        </linearGradient>
        <linearGradient id="toolTone" x1="0" y1="0" x2="0" y2="1">
          <stop offset="0" stop-color="#2a2a2a"/>
          <stop offset="1" stop-color="#111"/>
        </linearGradient>
      </defs>
      <polygon class="engine-photo" role="img" aria-label="Close-up photo of a car engine with pulleys and alternator"
               points="0,0 871,0 661,322 0,322" fill="url(#engineTone)"/>
      <polygon class="accent-stripe" points="871,0 918,0 673,322 661,322" fill="var(--brand-blue)"/>
      <rect class="wrench-art" role="img" aria-label="Two crossed white wrenches"
            x="845" y="224" width="338" height="98" rx="6" fill="url(#toolTone)"/>
    </svg>
    <ul class="services">
      <li><span class="dot">•</span>TIRES <span class="dot">•</span>SERVICE</li>
      <li><span class="dot">•</span>REPAIR <span class="dot">•</span>DIESEL</li>
    </ul>
    <p class="company-name">BREKWELL AUTOMOTIVE</p>
  </section>

  <div class="divider"></div>

  <footer class="contact-band">
    <span class="call-now">CALL NOW</span>
    <span class="phone">(555)314-2609</span>
    <span class="town">FUQUAY-VARINA</span>
  </footer>
</div>
</body>
</html>
```